WordPress Design for both website and landing page for an expert

I need a clean and stylish design for my new website. I work as an expert (see attached file WHY HOW WHAT), my product is expert opinion (reports) for company evaluations You can use all of the attached pictures colored or black / white. The person is me, you can add other pictures, if you want. The design should be clean and stylish, so you could use white, black, gray, silver and / or one additional color. I have added an idea about my website, see attached file CONCEPT WEBSITE If you have any more information, please do not hesitate to contact us 'Hesitate to ask me ...

```html
<!DOCTYPE html>
<html lang="de">
<head>
<meta charset="utf-8">
<title>Jonas Keller – Expert for Company Valuations</title>
<link href="https://fonts.googleapis.com/css2?family=Montserrat:wght@400;500;600;700&family=Raleway:wght@300;400;500&family=Open+Sans:wght@400;600&display=swap" rel="stylesheet">
<style>
:root{
  --black:#0b0b0b;
  --white:#ffffff;
  --grey-bg:#f2f2f2;
  --grey-line:#c9c9c9;
  --text:#333333;
  --text-soft:#666666;
  --blue:#1f4f9a;
  --blue-nav:#3f7fd6;
}
*{box-sizing:border-box;margin:0;padding:0}
html,body{width:1200px;height:3789px;overflow:hidden}
body{position:relative;background:var(--white);font-family:"Open Sans",Arial,sans-serif;color:var(--text)}
.abs{position:absolute}
.site-header{left:0;top:0;width:1200px;height:104px;background:var(--black)}
.brand{left:114px;top:38px;color:var(--white);font-family:"Raleway",sans-serif;font-size:20px;letter-spacing:3px;display:flex;align-items:center;gap:12px}
.brand-mark{width:24px;height:24px;border:2px solid var(--white);border-radius:50%}
.main-nav{right:112px;top:45px;display:flex;gap:48px;font-family:"Montserrat",sans-serif;font-size:12px;font-weight:600;color:var(--white);text-transform:uppercase}
.main-nav .active{color:var(--blue-nav)}
.hero{left:0;top:104px;width:1200px;height:566px;background:linear-gradient(180deg,#4e87c7 0%,#8fb5da 28%,#2a4466 52%,#1a2230 70%,#2b4b6e 100%)}
.hero-title{left:0;top:176px;width:1200px;text-align:center;color:var(--white);font-family:"Montserrat",sans-serif;font-weight:700;font-size:32px}
.hero-sub{left:0;top:226px;width:1200px;text-align:center;color:var(--white);font-family:"Raleway",sans-serif;font-size:30px;line-height:43px}
.reasons{left:0;top:670px;width:1200px;height:495px;background:linear-gradient(90deg,#ececec 0%,#f1f1f1 50%,#dcdcdc 100%)}
.portrait-reasons{left:600px;top:670px;width:600px;height:495px;background:linear-gradient(90deg,rgba(240,240,240,0) 0%,#c9c9c9 40%,#b8b8b8 100%)}
.section-title{font-family:"Raleway",sans-serif;font-weight:400;color:var(--text);text-transform:uppercase}
.rule{width:64px;height:2px;background:var(--blue)}
.reason{left:114px;width:492px;height:48px;background:#f4f4f4;border:1px solid var(--grey-line);display:flex;align-items:center;padding-left:16px;font-family:"Montserrat",sans-serif;font-size:17px;color:#222}
.reason small{font-family:"Open Sans",sans-serif;font-size:11px;color:var(--text-soft);margin-left:4px}
.quality-photo{left:0;top:1165px;width:580px;height:376px;background:linear-gradient(90deg,#8b8f95 0%,#c8cbcf 55%,#ffffff 100%)}
.body-copy{font-size:12px;line-height:28px;color:var(--text-soft)}
.btn-outline{left:609px;top:1412px;width:252px;height:38px;border:1.5px solid var(--blue);color:var(--blue);font-family:"Montserrat",sans-serif;font-weight:600;font-size:11px;display:flex;align-items:center;justify-content:center}
.feature{width:260px;text-align:center}
.feature .num{font-family:"Montserrat",sans-serif;font-size:76px;font-weight:500;color:#d6d6d6;line-height:1}
.feature h3{font-family:"Montserrat",sans-serif;font-weight:500;font-size:22px;color:#111;margin-top:4px}
.feature p{font-size:13px;line-height:23px;margin-top:14px;color:var(--text)}
.connector{height:2px;background:#222;width:150px}
.venn{left:160px;top:2138px;width:350px;height:340px;border-radius:50%;background:radial-gradient(circle at 50% 30%,#e6efd6 0%,#fdf1dc 45%,#dcedf8 75%,#ffffff 100%)}
.wiw h2{font-family:"Raleway",sans-serif;font-weight:400;font-size:34px;color:#222}
.wiw p{font-size:12px;line-height:26px;color:var(--text-soft);width:470px;margin-top:10px}
.about{left:0;top:2539px;width:1200px;height:720px;background:var(--grey-bg)}
.about-photo{left:147px;top:2602px;width:442px;height:590px;background:linear-gradient(180deg,#9b9b9b 0%,#5a5a5a 60%,#2e2e2e 100%)}
.about-card{left:528px;top:2655px;width:533px;height:485px;background:var(--white);box-shadow:0 2px 14px rgba(0,0,0,.12);padding:30px 40px}
.about-card h2{font-family:"Raleway",sans-serif;font-weight:400;font-size:34px;color:#222;text-transform:uppercase}
.about-card h4{font-family:"Montserrat",sans-serif;font-weight:600;font-size:14px;color:#222;margin-top:18px}
.about-card ul{list-style:none;font-size:11px;line-height:28px;color:var(--text-soft);margin-top:6px}
.partner-logo{width:140px;height:46px;background:#e6e6e6;border-radius:3px}
.contact{left:0;top:3259px;width:1200px;height:447px;background:linear-gradient(180deg,#f4f4f4 0%,#e9e9e9 100%)}
.field{background:var(--white);border:1px solid var(--grey-line);font-size:11px;color:var(--text);padding:12px 14px}
.submit{left:530px;top:3620px;width:139px;height:45px;background:var(--blue);color:var(--white);font-family:"Montserrat",sans-serif;font-weight:600;font-size:14px;display:flex;align-items:center;justify-content:center}
.site-footer{left:0;top:3706px;width:1200px;height:83px;background:var(--black);color:var(--white);font-size:12px;text-align:center;padding-top:30px}
</style>
</head>
<body>

<header class="abs site-header">
  <div class="abs brand"><span class="brand-mark"></span>JONAS KELLER</div>
  <nav class="abs main-nav"><span class="active">Home</span><span>What I do</span><span>Why I do it &amp; How I do it</span><span>About me</span><span>Contact</span></nav>
</header>

<section class="abs hero" role="img" aria-label="Evening city skyline with river and TV tower"></section>
<h1 class="abs hero-title">EXPERT FOR COMPANY VALUATIONS</h1>
<p class="abs hero-sub">Sie benötigen ein Gutachten zur Ermittlung des<br>Wertes Ihres Unternehmens</p>

<section class="abs reasons"></section>
<div class="abs portrait-reasons" role="img" aria-label="Portrait of the expert in white shirt leaning on a table"></div>
<h2 class="abs section-title" style="left:114px;top:742px;font-size:31px;line-height:44px;">What do you need or can<br>use a report for</h2>
<div class="abs rule" style="left:114px;top:846px"></div>
<div class="abs reason" style="top:887px">Reason 1 <small>: Buying/selling shares or entire companies</small></div>
<div class="abs reason" style="top:950px">Reason 2 <small>: Inheritance matters</small></div>
<div class="abs reason" style="top:1013px">Reason 3 <small>: Questions in gain compensations (in divorce)</small></div>

<div class="abs quality-photo" role="img" aria-label="Hand holding a pen over a checkbox form"></div>
<h2 class="abs section-title" style="left:609px;top:1254px;font-size:31px;">My quality promise</h2>
<div class="abs rule" style="left:609px;top:1306px"></div>
<p class="abs body-copy" style="left:609px;top:1330px;width:480px;">Mein Qualitätsversprechen: Sollte der avisierte Termin für die Erstellung des Gutachtens überschritten werden, erhalten Sie das Gutachten abso lut kostenfrei!</p>
<div class="abs btn-outline">ICH VERZICHTE AUF MEIN HONORAR</div>

<h2 class="abs section-title" style="left:0;top:1576px;width:1200px;text-align:center;font-size:31px;">Why choose us</h2>

<svg class="abs" style="left:198px;top:1662px" width="120" height="120" viewBox="0 0 120 120" fill="none" stroke="#111" stroke-width="5"><circle cx="60" cy="60" r="54"/><path d="M60 24v38l22 12" stroke-linecap="round"/></svg>
<div class="abs connector" style="left:354px;top:1726px"></div>
<svg class="abs" style="left:550px;top:1662px" width="100" height="120" viewBox="0 0 100 120" fill="none" stroke="#111" stroke-width="4"><path d="M50 6L90 20v38c0 30-22 48-40 56C32 106 10 88 10 58V20z"/><path d="M30 60l14 14 28-28" stroke-width="6"/></svg>
<div class="abs connector" style="left:690px;top:1726px"></div>
<svg class="abs" style="left:886px;top:1662px" width="120" height="120" viewBox="0 0 120 120" fill="none" stroke="#111" stroke-width="4"><path d="M10 4h54l20 20v90H10z"/><path d="M22 28h40M22 44h50M22 60h30M22 76h24"/><circle cx="78" cy="78" r="18"/><path d="M91 91l22 22" stroke-width="7" stroke-linecap="round"/></svg>

<div class="abs feature" style="left:128px;top:1800px"><div class="num">01</div><h3>Schnell</h3><p>Sie bekommen Ihr Gutachten zeitnah (innerhalb von max. 21 Tagen nach Zugang aller benötigten Unterlagen)</p></div>
<div class="abs feature" style="left:469px;top:1800px"><div class="num">02</div><h3>Zertifiziert</h3><p>Sie erhalten ein qualifiziertes und belastbares Gutachten von einem zertifizierten Sachverständigen (höchste Akzeptanz bei allen Parteien)</p></div>
<div class="abs feature" style="left:812px;top:1800px"><div class="num">03</div><h3>Verständlich</h3><p>Ihr Gutachten wird für Sie logisch und nachvollziehbar sein und kein "Fachchinesisch" enthalten</p></div>

<div class="abs venn" role="img" aria-label="Illustration of three overlapping circles for what, how and why"></div>

<div class="abs wiw" style="left:589px;top:2114px"><h2>WHAT I DO</h2><p>Conducting business valuations in case of ... Durchführung von Unternehmens bewertungen (Wertermittlung) bei</p></div>
<div class="abs wiw" style="left:589px;top:2246px"><h2>HOW I DO</h2><p>Jedes Gutachten beginnt mit Verstehen. Also stelle ich Ihnen Fragen und höre sehr genau zu.Bei der Erstellung jedes Gutachtens folge ich einem</p></div>
<div class="abs wiw" style="left:589px;top:2387px"><h2>WHY I DO</h2><p>Economy is my passion. Economy is made in numbers. Sometimes it is difficult to find the right numbers. I am always interested in finding out, how economy</p></div>

<section class="abs about"></section>
<div class="abs about-photo" role="img" aria-label="Black and white portrait of the expert in a suit"></div>
<div class="abs about-card">
  <h2>About Jonas M. Keller</h2>
  <div class="rule" style="margin-top:10px"></div>
  <h4>Professional Experience</h4>
  <ul><li>10 years as managing director in the fitness market</li><li>10 years as CMO / business trainer / CEO in an german industrial company</li><li>Outside lecturer at HBW Nord</li><li>expert Norvex</li></ul>
  <div style="display:flex;justify-content:space-between">
    <div><h4>Educations</h4>
      <ul><li>Bankkaufmann Kammer</li><li>staat. Geprüfter Betriebswirt (BA)</li><li>Dipl. Kfm. (FH)</li><li>Business Trainer TVN</li><li>Lizenzierter Fitnesstrainer FSV</li><li>Sachverständiger für Unternehmensbewertungen</li></ul></div>
    <div style="width:160px"><h4>Our Partners</h4>
      <div style="margin-top:20px;font-family:'Montserrat',sans-serif;font-weight:700;font-size:26px;color:#1d2f5c">Norvex</div>
      <div class="partner-logo" style="margin-top:22px"></div></div>
  </div>
</div>

<section class="abs contact" role="img" aria-label="Faint background of a pen on printed figures"></section>
<h2 class="abs section-title" style="left:0;top:3294px;width:1200px;text-align:center;font-size:31px;">Contact us</h2>
<div class="abs rule" style="left:568px;top:3344px"></div>
<p class="abs body-copy" style="left:290px;top:3360px;width:620px;text-align:center;">Sed ut perspiciatis unde omnis iste natus error sit voluptatem accusantium doloremque laudantium, totam remo inventore veritatis et quasi architecto beatae vitae dicta sunt explicabo.</p>
<div class="abs field" style="left:296px;top:3443px;width:300px;height:44px">First Name :</div>
<div class="abs field" style="left:604px;top:3443px;width:300px;height:44px">Last Name :</div>
<div class="abs field" style="left:296px;top:3496px;width:300px;height:44px">Phone :</div>
<div class="abs field" style="left:604px;top:3496px;width:300px;height:44px">Email :</div>
<div class="abs field" style="left:296px;top:3549px;width:608px;height:58px">Message :</div>
<div class="abs submit">SUBMIT</div>

<footer class="abs site-footer">© Copyrights 2018 - Jonas Keller All Rights Reserved.</footer>

</body>
</html>
```